sydney wedding photography business needs a business card design

we need a business card design for a sydney based wedding photography and videography business. our business name is :golden hour studio and film. our target clients are 24-35 yrs female. our style is candid, organic, natural, dynamic. we are a team of young photographers and videographers, and help brides to create memories that they will cherish for the rest of their lives. the logo will be provided. we want an elegant design that reflects our style, and also want to give a great impression to our clients that we are one of the best studios in sydney and our brand means quality and premium service.

Target Market(s)

bride to be, 24-35 years old, living in sydney and surrunding areas

Industry/Entity Type

Wedding Photography

Contact Information for Business Card

address: 57 tarrant street, glenmore nsw 2047
mobile: 0431872259
phone: (02) 9163 2408
info@tidewillowstudio.net.au
www.tidewillowstudio.net.au
facebook:tidewillowweddings
instagram:tidewillowweddings

Font styles to use
Serif
Sans Serif

Requirements
Nice to have
• maybe add my slogan"memories beyond eternity" if the layout looks good
Should not have
• no black color, not good idea for wedding biz card

```html
<!DOCTYPE html>
<html lang="en">
<head>
<meta charset="utf-8">
<title>Golden Hour Studio and Film – Business Card</title>
<link href="https://fonts.googleapis.com/css2?family=Open+Sans:wght@400;600&display=swap" rel="stylesheet">
<style>
  :root {
    --backdrop: #a6a6a6;
    --card-white: #ffffff;
    --card-gold: #d4a00f;
    --gold-ink: #c9960e;
    --text-dark: #3a3a3a;
    --rule: #9a9a9a;
    --icon-deep: #3b2f0a;
  }
  * { margin: 0; padding: 0; box-sizing: border-box; }
  html, body {
    width: 1200px; height: 900px; overflow: hidden;
    background: var(--backdrop);
    font-family: "Open Sans", Arial, sans-serif;
  }
  .stage { position: relative; width: 1200px; height: 900px; }

  .card {
    position: absolute; top: 306px;
    width: 440px; height: 272px;
    border-radius: 12px;
  }
  .card--front { left: 149px; background: var(--card-white); }
  .card--back  { left: 608px; background: var(--card-gold); }

  .wordmark {
    position: absolute; left: 0; right: 0;
    text-align: center; color: var(--gold-ink);
    font-weight: 600;
  }
  .wordmark__name { display: block; font-size: 34px; line-height: 40px; }
  .wordmark__sub  { display: block; font-size: 13px; letter-spacing: 5px; line-height: 18px; }
  .card--front .wordmark { top: 44px; }
  .card--back .wordmark { top: 92px; color: #f1d27a; }

  .address {
    position: absolute; left: 28px; top: 143px;
    font-size: 12px; line-height: 15px; color: var(--text-dark);
  }
  .holder {
    position: absolute; right: 36px; top: 165px; text-align: right;
  }
  .holder__name { font-size: 14px; font-weight: 600; color: var(--gold-ink); line-height: 18px; }
  .holder__role { font-size: 11.5px; color: var(--text-dark); line-height: 16px; margin-top: 4px; }
  .divider {
    position: absolute; left: 28px; top: 185px;
    width: 376px; height: 1px; background: var(--rule);
  }
  .contacts {
    position: absolute; left: 27px; top: 196px; list-style: none;
    font-size: 12px; line-height: 16px; color: var(--text-dark);
  }
  .contacts li { display: flex; align-items: center; gap: 6px; }
  .contacts svg { width: 10px; height: 10px; fill: var(--gold-ink); }

  .social {
    position: absolute; top: 208px; left: 0; right: 0;
    display: flex; justify-content: center; gap: 12px;
  }
  .social__dot {
    width: 26px; height: 26px; border-radius: 50%;
    background: var(--icon-deep);
  }
</style>
</head>
<body>
<main class="stage">

  <section class="card card--front">
    <div class="wordmark">
      <span class="wordmark__name">Golden Hour</span>
      <span class="wordmark__sub">STUDIO AND FILM</span>
    </div>

    <p class="address">57 tarrant street,<br>glenmore nsw 2047</p>

    <div class="holder">
      <p class="holder__name">Daniel Archer</p>
      <p class="holder__role">Managing Director</p>
    </div>
    <div class="divider"></div>

    <ul class="contacts">
      <li>
        <svg viewBox="0 0 10 10" aria-hidden="true"><path d="M2 0.5 L3.6 2.6 L2.8 3.6 Q4 6 6.4 7.2 L7.4 6.4 L9.5 8 L8.4 9.5 Q3.5 9 0.5 1.6 Z"/></svg>
        0431 872 259
      </li>
      <li>
        <svg viewBox="0 0 10 10" aria-hidden="true"><rect x="0.5" y="2" width="9" height="6.5" rx="0.8"/><path d="M0.8 2.4 L5 5.6 L9.2 2.4" stroke="#fff" stroke-width="0.9" fill="none"/></svg>
        info@tidewillowstudio.net.au
      </li>
      <li>
        <svg viewBox="0 0 10 10" aria-hidden="true"><circle cx="5" cy="5" r="4.5"/><path d="M0.8 5 H9.2 M5 0.6 Q2.4 5 5 9.4 M5 0.6 Q7.6 5 5 9.4" stroke="#fff" stroke-width="0.7" fill="none"/></svg>
        www.tidewillowstudio.net.au
      </li>
    </ul>
  </section>

  <section class="card card--back">
    <div class="wordmark">
      <span class="wordmark__name">Golden Hour</span>
      <span class="wordmark__sub">STUDIO AND FILM</span>
    </div>
    <div class="social" aria-label="Social media links">
      <span class="social__dot"></span>
      <span class="social__dot"></span>
      <span class="social__dot"></span>
      <span class="social__dot"></span>
    </div>
  </section>

</main>
</body>
</html>
```